Korval Advise Business Cards

We need a business card design for Korval Advise (Logo Attached), a management consultancy specialized in brand & business building.

Design should be clean, smart and a touch of innnovation without being gimmicky.

The details on the card should be:
Name: Tomas Velduren
Title: Managing Director
Address: 42 Marlowe Pier, Tarn Vessel Tower, Singapore 073926
Tel: +6285927461082
email: tv@korvaladvise.example
website: korvaladvise.example

For further background on corporate identity, please check www.korvaladvise.example
Updates

Dear all,

Many thanks for the submissions so far! I gave feedback to those designs that I prefer at this stage.

Overall I see that my preference goes into the direction that 'less is more' and 'simple is beautiful'

Please create uniqueness and standout by the simplicity and attraction of the overall concept and design.

Many thanks and please shout incase of questions!

Tomas

Industry/Entity Type

Business

```html
<!DOCTYPE html>
<html lang="en">
<head>
<meta charset="utf-8">
<title>Korval Advise Business Cards</title>
<link rel="stylesheet" href="https://fonts.googleapis.com/css2?family=Source+Sans+3:wght@400;600;700&display=swap">
<style>
  :root {
    --backdrop: #e9e7e4;
    --card: #ffffff;
    --charcoal: #4a4a4c;
    --orange: #f46a0f;
    --white: #ffffff;
  }
  * { margin: 0; padding: 0; box-sizing: border-box; }
  html, body { width: 1173px; height: 1200px; overflow: hidden; }
  body {
    background: var(--backdrop);
    font-family: "Source Sans 3", Arial, sans-serif;
    position: relative;
  }
  .card {
    position: absolute;
    background: var(--card);
    overflow: hidden;
    box-shadow: 0 2px 8px rgba(0,0,0,0.18);
  }
  .card--front { left: 207px; top: 30px; width: 943px; height: 542px; }
  .card--back { left: 25px; top: 622px; width: 941px; height: 536px; }

  .brand {
    position: absolute;
    color: var(--charcoal);
    font-weight: 600;
    font-size: 76px;
    line-height: 1;
    letter-spacing: 1px;
    white-space: nowrap;
  }
  .card--front .brand { left: 63px; top: 70px; }
  .card--back .brand { left: 0; right: 0; top: 236px; text-align: center; }

  .swoosh { position: absolute; left: 0; top: 0; width: 943px; height: 542px; }

  .holder { position: absolute; left: 63px; top: 226px; }
  .holder__name { color: var(--charcoal); font-weight: 700; font-size: 29px; line-height: 36px; }
  .holder__title { color: var(--orange); font-size: 24px; line-height: 30px; }
  .address {
    position: absolute; left: 63px; top: 326px;
    color: var(--charcoal); font-size: 23px; line-height: 32px; font-style: normal;
  }
  .contacts {
    position: absolute; right: 30px; top: 420px;
    list-style: none; text-align: right;
    color: var(--white); font-size: 23px; line-height: 40px;
  }
  .contacts li { display: flex; justify-content: flex-end; align-items: center; gap: 8px; }
  .contacts svg { width: 18px; height: 18px; }

  .back__url {
    position: absolute; left: 0; right: 0; top: 400px;
    text-align: center; color: var(--charcoal);
    font-size: 26px; letter-spacing: 5px;
  }
</style>
</head>
<body>
  <section class="card card--front">
    <svg class="swoosh" viewBox="0 0 943 542" aria-hidden="true">
      <path fill="var(--charcoal)" d="M943 262 C800 280 660 400 540 470 C470 510 400 535 330 542 L943 542 Z"/>
      <path fill="var(--orange)" d="M0 440 C140 470 300 505 430 470 C600 420 760 258 943 222 L943 238 C770 272 630 420 460 500 C320 552 150 520 0 492 Z"/>
      <path fill="var(--orange)" d="M0 505 C120 530 240 545 330 542 L0 542 Z"/>
    </svg>

    <p class="brand">Korval Advise</p>

    <div class="holder">
      <p class="holder__name">Tomas Velduren</p>
      <p class="holder__title">Managing Director</p>
    </div>

    <address class="address">
      42 Marlowe Pier, Tarn<br>Vessel Tower, Singapore 073926
    </address>

    <ul class="contacts">
      <li>
        <svg viewBox="0 0 20 20" aria-hidden="true"><path fill="none" stroke="#fff" stroke-width="2" d="M5 2 L8 6 L6 8 C7 11 9 13 12 14 L14 12 L18 15 L16 18 C9 18 2 11 2 4 Z"/></svg>
        <span>+6285927461082</span>
      </li>
      <li>
        <svg viewBox="0 0 20 20" aria-hidden="true"><rect x="2" y="6" width="16" height="11" fill="#fff"/><path d="M2 6 L10 12 L18 6" fill="none" stroke="var(--charcoal)" stroke-width="1.5"/></svg>
        <span>tv@korvaladvise.example</span>
      </li>
      <li>
        <svg viewBox="0 0 20 20" aria-hidden="true"><g fill="none" stroke="#fff" stroke-width="1.6"><circle cx="10" cy="10" r="8"/><ellipse cx="10" cy="10" rx="3.5" ry="8"/><path d="M2 10 H18"/></g></svg>
        <span>www.korvaladvise.example</span>
      </li>
    </ul>
  </section>

  <section class="card card--back">
    <p class="brand">Korval Advise</p>
    <p class="back__url">www.korvaladvise.example</p>
  </section>
</body>
</html>
```